Construction company business card

One side to be the logo with the company name, The other side I would like: (Tomas verbick) Project manager 41 barrow crescent hallam 52917306224783(03) 9703 2428Info@gudeljgroup.comAnd then maybe a couple dot points saying what we do:Construction (commercial & industrial) Civil construction

Anything else please contact me!
Maybe curved st one edge of the card

Target Market(s)

Older clientele

Industry/Entity Type

Construction Company

Contact Information for Business Card

Read above

Colors
3277b5
1b1b1b
9d9d9d

Requirements
Must have
• Use my logo on one side
Nice to have
• Read above
Should not have
• Read above

```html
<!DOCTYPE html>
<html lang="en">
<head>
<meta charset="utf-8">
<title>Ridgeline Construction – Business Card</title>
<link rel="stylesheet" href="https://fonts.googleapis.com/css2?family=Work+Sans:wght@400;600&display=swap">
<style>
  :root {
    --brand-blue: #1a5faf;
    --brand-blue-light: #2a74c0;
    --ink-mid: #5c5c5c;
    --band-grey: #4b4b4b;
    --card-white: #ffffff;
    --backdrop: #dcdcdc;
  }
  * { box-sizing: border-box; margin: 0; padding: 0; }
  html, body { width: 1200px; height: 930px; overflow: hidden; }
  body {
    background: var(--backdrop);
    font-family: "Work Sans", Arial, sans-serif;
    position: relative;
  }
  .card {
    position: absolute;
    width: 600px;
    height: 343px;
    border-radius: 28px;
    overflow: hidden;
    box-shadow: 0 6px 18px rgba(0,0,0,0.18);
  }
  .card-front {
    left: 120px; top: 90px;
    background: linear-gradient(135deg, var(--brand-blue-light), var(--brand-blue));
    display: flex; align-items: center; justify-content: center;
  }
  .wordmark {
    display: flex; align-items: center; gap: 16px;
    font-weight: 600;
    text-transform: uppercase;
  }
  .wordmark-dot { width: 54px; height: 54px; border-radius: 50%; flex: none; }
  .wordmark-text { line-height: 1.05; letter-spacing: 2px; }
  .wordmark-text .line-main { display: block; font-size: 40px; }
  .wordmark-text .line-sub { display: block; font-size: 17px; letter-spacing: 6px; }
  .card-front .wordmark { color: var(--card-white); }
  .card-front .wordmark-dot { background: var(--card-white); }

  .card-back { left: 480px; top: 495px; background: var(--card-white); }
  .card-back .wordmark {
    position: absolute; left: 44px; top: 150px;
    gap: 12px;
    color: var(--brand-blue);
  }
  .card-back .wordmark-dot { background: var(--brand-blue); width: 42px; height: 42px; }
  .card-back .wordmark-text .line-main { font-size: 28px; }
  .card-back .wordmark-text .line-sub { font-size: 12px; letter-spacing: 4px; }

  .divider {
    position: absolute; left: 300px; top: 92px;
    width: 2px; height: 150px; background: var(--brand-blue);
  }
  .contact {
    position: absolute; left: 328px; top: 84px;
    color: var(--ink-mid);
    font-size: 14px; line-height: 1.4;
  }
  .contact-name {
    color: var(--brand-blue); font-weight: 600;
    font-size: 20px; letter-spacing: 0.5px; text-transform: uppercase;
  }
  .contact-role { font-size: 15px; margin-bottom: 8px; }
  .contact-address { padding-left: 22px; margin-bottom: 8px; }
  .contact-list { list-style: none; }
  .contact-list li { display: flex; align-items: center; gap: 8px; }
  .contact-list svg { width: 12px; height: 12px; flex: none; }
  .edge-band { position: absolute; left: 0; bottom: 0; width: 600px; height: 10px; }
</style>
</head>
<body>
  <section class="card card-front" aria-label="Card front">
    <div class="wordmark">
      <span class="wordmark-dot"></span>
      <span class="wordmark-text"><span class="line-main">Ridgeline</span><span class="line-sub">Construction</span></span>
    </div>
  </section>

  <section class="card card-back" aria-label="Card back">
    <div class="wordmark">
      <span class="wordmark-dot"></span>
      <span class="wordmark-text"><span class="line-main">Ridgeline</span><span class="line-sub">Construction</span></span>
    </div>
    <div class="divider"></div>
    <div class="contact">
      <p class="contact-name">Tomas Verbick</p>
      <p class="contact-role">Project manager</p>
      <p class="contact-address">41 barrow<br>crescent kelvinbrook 5291</p>
      <ul class="contact-list">
        <li><svg viewBox="0 0 12 12"><path d="M3 1l2 2-1 1.5c.8 1.6 2 2.8 3.5 3.5L9 7l2 2-1.5 2C5 10.5 1.5 7 1 2.5z" fill="var(--brand-blue)"/></svg>73 0622 4783</li>
        <li><svg viewBox="0 0 12 12"><rect x="3" y="1" width="6" height="10" rx="1" fill="none" stroke="var(--brand-blue)" stroke-width="1.4"/></svg>03 9418 6573</li>
        <li><svg viewBox="0 0 12 12"><rect x="1" y="3" width="10" height="7" fill="none" stroke="var(--brand-blue)" stroke-width="1.2"/><path d="M1 3l5 4 5-4" fill="none" stroke="var(--brand-blue)" stroke-width="1.2"/></svg>Info@verbickgroup.com</li>
      </ul>
    </div>
    <svg class="edge-band" viewBox="0 0 600 10" preserveAspectRatio="none" aria-hidden="true">
      <polygon points="0,0 392,0 386,10 0,10" fill="var(--brand-blue)"/>
      <polygon points="396,0 600,0 600,10 390,10" fill="var(--band-grey)"/>
    </svg>
  </section>
</body>
</html>
```